Meadowrun Acres Website Design

We have been redeveloping our website already and are quite happy with the content, but the design needs to be better:
https://tilvexa-hub.examplehost.net/

Pages, content, concept etc. Can all be taken from the redeveloped website.
The farmer can register and edit/view their profile, subscribe and these pages need to be designed better as well as contact, about, pricing, tos, privacy and a page with example portlets.

We need a website to appeal to farmers, investors and retiring farmers.

The design should be clean and a little country.

We don't want any repeat designs that some may submit to every project and has no respect for the project brief, so please don't submit them.

Target Market(s)

farmers, investors, retirees

Industry/Entity Type

Farming

Number of Pages Required

5+ page

Colors

Designer to choose colors to be used in the design.

Requirements
Must have
• Nice, clean modern design that is appealing
• Profile page laid out nicely

```html
<!DOCTYPE html>
<html lang="en">
<head>
<meta charset="utf-8">
<title>Meadowrun Acres – Farmers</title>
<link href="https://fonts.googleapis.com/css2?family=Roboto:wght@300;400;500;700&display=swap" rel="stylesheet">
<style>
:root{
  --green:#2f7d32;
  --green-dark:#236127;
  --green-light:#e8f3e8;
  --orange:#f7931e;
  --ink:#333;
  --muted:#777;
  --line:#dcdcdc;
  --footer:#2a2a2a;
  --footer-2:#1f1f1f;
}
*{box-sizing:border-box;margin:0;padding:0}
html,body{width:1200px;height:5172px;overflow:hidden}
body{font-family:'Roboto',Arial,sans-serif;color:var(--ink);background:#fff;position:relative}
.abs{position:absolute}
.btn-orange{background:var(--orange);color:#fff;font-weight:700;font-size:13px;text-transform:uppercase;letter-spacing:.5px;border-radius:3px;display:flex;align-items:center;justify-content:center}

/* header */
.site-header{position:absolute;top:0;left:0;width:1200px;height:72px;background:#fff;display:flex;align-items:center;padding:0 72px;border-bottom:1px solid #eee}
.brand{display:flex;align-items:center;gap:10px;font-weight:700;color:var(--green);font-size:18px}
.brand .dot{width:22px;height:22px;border-radius:50%;background:var(--green)}
.main-nav{margin-left:auto;display:flex;gap:22px;font-size:12px;font-weight:500;text-transform:uppercase;color:#444}
.main-nav .active{color:var(--green);border-bottom:2px solid var(--green);padding-bottom:4px}
.nav-cta{margin-left:26px;color:var(--orange);font-size:12px;font-weight:700;text-transform:uppercase}

.hero{position:absolute;top:72px;left:0;width:1200px;height:328px;background:linear-gradient(180deg,#6d8a5a 0%,#4e6b3e 55%,#3a4f2e 100%)}
.hero h1{position:absolute;top:130px;width:100%;text-align:center;color:#fff;font-weight:300;font-size:48px}
.breadcrumb{position:absolute;top:404px;left:72px;font-size:12px;color:var(--muted)}
.breadcrumb span{color:var(--green)}

/* profile slider */
.slider{position:absolute;top:448px;left:72px;width:1056px;height:352px;background:var(--green)}
.slider .photo{position:absolute;left:40px;top:24px;width:448px;height:304px;background:linear-gradient(135deg,#8a6d4b,#5b7d45)}
.slider .copy{position:absolute;left:528px;top:60px;width:460px;color:#fff}
.slider h3{font-size:26px;font-weight:500;text-align:center;margin-bottom:20px}
.slider p{font-size:15px;line-height:1.6;color:#e8f1e8}
.slider .btn-orange{width:150px;height:38px;margin-top:22px}
.slider .arrow{position:absolute;top:152px;width:28px;height:48px;background:rgba(0,0,0,.45);display:flex;align-items:center;justify-content:center}

/* new family */
.new-family{position:absolute;top:840px;left:72px;width:520px;height:300px;border:5px solid var(--green);text-align:center;padding:40px 30px}
.new-family h3{font-size:26px;font-weight:400;color:var(--green);line-height:1.2}
.new-family .sub{font-size:18px;color:#555;margin:6px 0 14px}
.new-family p{font-size:14px;color:#666;line-height:1.5}
.new-family .btn-orange{height:42px;margin-top:24px}
.video{position:absolute;top:840px;left:612px;width:516px;height:300px;background:linear-gradient(160deg,#596b4a,#2d3426)}
.video .play{position:absolute;left:218px;top:110px;width:80px;height:80px;border-radius:50%;background:rgba(0,0,0,.6);display:flex;align-items:center;justify-content:center}

/* how it works */
.section-title{position:absolute;left:0;width:1200px;text-align:center;font-size:24px;font-weight:500;color:#333}
.section-title::after{content:"";display:block;width:40px;height:3px;background:var(--green);margin:10px auto 0}
.steps{position:absolute;top:1236px;left:96px;width:1010px;list-style:none}
.steps li{position:relative;padding-left:26px;font-size:14px;line-height:1.55;color:#555;margin-bottom:22px}
.steps li::before{content:"";position:absolute;left:0;top:7px;width:8px;height:8px;background:var(--green);border-radius:50%}

/* bands */
.band{position:absolute;left:72px;width:1056px;height:312px;background:var(--green)}
.band .pics{position:absolute;top:24px;left:24px;display:flex;gap:16px}
.band .pic{width:325px;height:200px}
.band h2{position:absolute;top:240px;width:100%;text-align:center;color:#fff;font-size:28px;font-weight:400}
.p1{background:linear-gradient(180deg,#9fb6cf,#6c8f4e)}
.p2{background:linear-gradient(180deg,#c9d3c2,#7d8f52)}
.p3{background:linear-gradient(180deg,#8fb0d6,#4f7a3a)}

/* benefits */
.benefits-line{position:absolute;left:599px;top:2150px;width:2px;height:640px;background:var(--line)}
.benefit-icon{position:absolute;left:564px;width:72px;height:72px;border-radius:50%;background:#fff;border:3px solid var(--green);display:flex;align-items:center;justify-content:center}
.benefit-text{position:absolute;width:300px}
.benefit-text h4{font-size:16px;font-weight:700;color:#333}
.benefit-text p{font-size:13px;color:var(--muted);margin-top:4px}
.benefit-text.left{left:250px;text-align:right}
.benefit-text.right{left:660px}

/* expectations */
.exp-label{position:absolute;width:240px;text-align:center}
.exp-label h4{font-size:16px;font-weight:700;color:#333}
.exp-label p{font-size:13px;color:var(--muted);margin-top:4px;line-height:1.4}

/* membership */
.membership{position:absolute;top:3832px;left:72px;width:1056px;height:208px;background:#ececec;text-align:center;padding:34px 80px}
.membership h3{font-size:24px;font-weight:500;color:#333}
.membership p{font-size:14px;color:#666;margin-top:14px;line-height:1.5}
.tips{position:absolute;top:4072px;left:72px;width:1056px;display:grid;grid-template-columns:repeat(3,1fr);gap:16px 24px}
.tip{height:56px;background:var(--green);color:#fff;font-size:15px;display:flex;align-items:center;justify-content:space-between;padding:0 16px 0 20px}
.tip .info{width:26px;height:26px;border-radius:50%;background:var(--green-dark);border:1px solid #fff;font-size:13px;font-weight:700;display:flex;align-items:center;justify-content:center}

/* footer */
.site-footer{position:absolute;top:4840px;left:0;width:1200px;height:332px;background:var(--footer);color:#ddd}
.site-footer h5{font-size:15px;font-weight:700;color:#fff;margin-bottom:20px}
.blog{position:absolute;left:72px;top:36px;width:400px}
.post{display:flex;gap:16px;margin-bottom:20px}
.post .date{width:56px;height:56px;background:var(--green);color:#fff;text-align:center;flex:none}
.post .date b{display:block;font-size:24px;line-height:36px}
.post .date small{font-size:10px;text-transform:uppercase}
.post h6{font-size:14px;font-weight:700;color:#fff;line-height:1.35}
.post span{font-size:12px;color:#999}
.subscribe{position:absolute;left:500px;top:36px;width:320px}
.subscribe p{font-size:13px;color:#aaa;line-height:1.5}
.subscribe .field{margin-top:14px;height:38px;background:#fff;border-radius:20px;font-size:13px;color:#999;padding:11px 18px}
.subscribe .btn-orange{width:110px;height:34px;border-radius:18px;margin-top:12px}
.footer-brand{position:absolute;left:920px;top:80px;display:flex;align-items:center;gap:12px;font-size:22px;font-weight:400;color:#fff}
.footer-brand .dot{width:26px;height:26px;border-radius:50%;border:2px solid #fff}
.footer-bottom{position:absolute;left:0;top:272px;width:1200px;height:60px;background:var(--footer-2);display:flex;align-items:center;padding:0 72px;font-size:12px;color:#999}
.socials{margin-left:auto;display:flex;gap:10px}
.socials i{width:26px;height:26px;border-radius:50%;background:#555;display:block}
</style>
</head>
<body>

<header class="site-header">
  <div class="brand"><span class="dot"></span>Meadowrun Acres</div>
  <nav class="main-nav">
    <span>Home</span><span class="active">Existing Farmers</span><span>Investors</span><span>Retiring Farmer</span><span>Blog</span><span>Pricing</span><span>Contact</span>
  </nav>
  <span class="nav-cta">Sign in or sign up</span>
</header>

<section class="hero" role="img" aria-label="Farming families standing together on their farm">
  <h1>Farmers</h1>
</section>
<div class="breadcrumb"><span>Home</span> / Farmers</div>

<section class="slider">
  <div class="photo" role="img" aria-label="Farming couple standing in their farm shed"></div>
  <div class="copy">
    <h3>Tom Halloway &amp; Ana Reyes</h3>
    <p>I really love to farm as farming is home. I would love to farm somewhere there is an opportunity to live and work in a local farming community.</p>
    <div class="btn-orange">View profile</div>
  </div>
  <div class="arrow" style="left:0"><svg width="12" height="18"><path d="M10 2 3 9l7 7" stroke="#fff" stroke-width="3" fill="none"/></svg></div>
  <div class="arrow" style="right:0"><svg width="12" height="18"><path d="M2 2l7 7-7 7" stroke="#fff" stroke-width="3" fill="none"/></svg></div>
</section>

<section class="new-family">
  <h3>New Farming Family</h3>
  <div class="sub">Want to own and operate your own farm?</div>
  <p>If you have a farming passion to be a farmer and think you are up for it then sign up to make your farm dream a reality.</p>
  <div class="btn-orange">Sign up now and lets get you farming!</div>
</section>
<div class="video" role="img" aria-label="Video of a young farmer talking about farm ownership">
  <div class="play"><svg width="30" height="30"><path d="M8 4l18 11L8 26z" fill="#fff"/></svg></div>
</div>

<h2 class="section-title" style="top:1180px">The Way It Works</h2>
<ol class="steps">
  <li>Together we find farm ownership opportunities for you. If farms meet your criteria and then we will match you with the retiring farmer and investors suit together – you even set the best farming arrangement.</li>
  <li>Our focus will be to ensure you have a good farm experience, so we will be with you the whole way.</li>
  <li>Our aim is to ensure that you are equity owner (with as little as 1%), receive a wage and annual incentives, and have the ongoing support of farming experts.</li>
  <li>We advocate for you to government, industry and to the public in order to help find you farms and grow farm equity opportunities.</li>
  <li>We cannot guarantee you will find your dream farm straight away as it may take years but we will always be looking and helping you get farm ready in the meantime.</li>
  <li>Your future farm is also in your hands. If you find a retiring farmer who is eager to work with you on a farm transition arrangement we can help you make this happen. This might be the quickest way for you to realise your farming dream.</li>
  <li>We ensure the best farming arrangement for you and your family and we can provide ongoing support once you have been matched.</li>
</ol>

<section class="band" style="top:1712px">
  <div class="pics">
    <div class="pic p1" role="img" aria-label="Cattle grazing in a green paddock"></div>
    <div class="pic p2" role="img" aria-label="Tractor working a field"></div>
    <div class="pic p3" role="img" aria-label="Rolling farmland under blue sky"></div>
  </div>
  <h2>Your Farm Dream Can Be A Reality.</h2>
</section>

<h2 class="section-title" style="top:2064px">Benefits</h2>
<div class="benefits-line"></div>

<div class="benefit-text left" style="top:2158px"><h4>Dream</h4><p>Finally live your farm dream</p></div>
<div class="benefit-icon" style="top:2150px"><svg width="34" height="34" viewBox="0 0 24 24"><path d="M12 21s-8-5.2-8-11a4.5 4.5 0 0 1 8-2.8A4.5 4.5 0 0 1 20 10c0 5.8-8 11-8 11z" fill="none" stroke="#2f7d32" stroke-width="2"/></svg></div>

<div class="benefit-icon" style="top:2254px"><svg width="34" height="34" viewBox="0 0 24 24"><path d="M3 11 12 3l9 8v10h-6v-6H9v6H3z" fill="#2f7d32"/></svg></div>
<div class="benefit-text right" style="top:2262px"><h4>Ownership</h4><p>Own your farm by being an equity partner</p></div>

<div class="benefit-text left" style="top:2366px"><h4>Income</h4><p>Receive a good wage</p></div>
<div class="benefit-icon" style="top:2358px"><svg width="34" height="34" viewBox="0 0 24 24"><rect x="2" y="6" width="20" height="12" rx="1" fill="#2f7d32"/><circle cx="12" cy="12" r="3" fill="#fff"/></svg></div>

<div class="benefit-icon" style="top:2462px"><svg width="34" height="34" viewBox="0 0 24 24"><path d="M14.5 3a5 5 0 0 0-4.6 6.8L3 16.7 6.3 20l6.9-6.9A5 5 0 0 0 20 8.5l-3 3-3.5-1-1-3.5 3-3z" fill="#2f7d32"/></svg></div>
<div class="benefit-text right" style="top:2470px"><h4>Manage</h4><p>Run the farm</p></div>

<div class="benefit-text left" style="top:2574px"><h4>Support</h4><p>Be supported for success by the best advisors</p></div>
<div class="benefit-icon" style="top:2566px"><svg width="34" height="34" viewBox="0 0 24 24"><path d="M6.6 10.8a15 15 0 0 0 6.6 6.6l2.2-2.2a1 1 0 0 1 1-.25 11.4 11.4 0 0 0 3.6.57 1 1 0 0 1 1 1V20a1 1 0 0 1-1 1A17 17 0 0 1 3 4a1 1 0 0 1 1-1h3.5a1 1 0 0 1 1 1c0 1.25.2 2.45.57 3.57a1 1 0 0 1-.25 1z" fill="#2f7d32"/></svg></div>

<div class="benefit-icon" style="top:2670px"><svg width="34" height="34" viewBox="0 0 24 24"><path d="M3 20h18M5 16l5-5 4 3 6-7" fill="none" stroke="#2f7d32" stroke-width="2.4"/></svg></div>
<div class="benefit-text right" style="top:2678px"><h4>Incentives</h4><p>Build your equity over time</p></div>

<div class="btn-orange abs" style="top:2820px;left:450px;width:300px;height:36px">Sign up now and lets get you farming</div>

<h2 class="section-title" style="top:2944px">Expectations</h2>
<svg class="abs" style="top:3040px;left:0" width="1200" height="740" viewBox="0 3040 1200 740">
  <g fill="none" stroke="#cfcfcf" stroke-width="3">
    <path d="M60 3200 H1140"/>
    <path d="M60 3600 H1140"/>
    <path d="M1140 3200 Q1180 3400 1140 3600"/>
  </g>
  <circle cx="150" cy="3200" r="48" fill="#2f7d32"/>
  <path d="M150 3222s-22-14-22-29a11 11 0 0 1 22-5 11 11 0 0 1 22 5c0 15-22 29-22 29z" fill="#fff"/>
  <circle cx="450" cy="3200" r="48" fill="#fff" stroke="#2f7d32" stroke-width="3"/>
  <circle cx="440" cy="3192" r="12" fill="none" stroke="#2f7d32" stroke-width="6" stroke-dasharray="5 3"/>
  <circle cx="464" cy="3212" r="8" fill="none" stroke="#2f7d32" stroke-width="5" stroke-dasharray="4 2"/>
  <circle cx="750" cy="3200" r="48" fill="#2f7d32"/>
  <path d="M730 3178h32a4 4 0 0 1 4 4v40h-32a4 4 0 0 1-4-4z" fill="#fff"/>
  <path d="M738 3190h20M738 3200h20" stroke="#2f7d32" stroke-width="3"/>
  <circle cx="1050" cy="3200" r="48" fill="#fff" stroke="#2f7d32" stroke-width="3"/>
  <rect x="1024" y="3186" width="52" height="28" fill="#2f7d32"/>
  <circle cx="1050" cy="3200" r="7" fill="#fff"/>
  <circle cx="150" cy="3600" r="48" fill="#fff" stroke="#2f7d32" stroke-width="3"/>
  <g fill="#2f7d32"><circle cx="134" cy="3600" r="8"/><circle cx="166" cy="3584" r="8"/><circle cx="166" cy="3616" r="8"/></g>
  <path d="M134 3600l32-16M134 3600l32 16" stroke="#2f7d32" stroke-width="3"/>
  <circle cx="450" cy="3600" r="48" fill="#2f7d32"/>
  <g fill="#fff"><circle cx="450" cy="3588" r="9"/><path d="M434 3616a16 12 0 0 1 32 0z"/><circle cx="428" cy="3594" r="6"/><circle cx="472" cy="3594" r="6"/></g>
  <circle cx="750" cy="3600" r="48" fill="#fff" stroke="#2f7d32" stroke-width="3"/>
  <path d="M726 3622v-24l14 8v-8l14 8v-8l14 8v-20h6v36z" fill="#2f7d32"/>
  <circle cx="1050" cy="3600" r="48" fill="#2f7d32"/>
  <path d="M1020 3594l30-14 30 14-30 14z M1034 3602v12c8 6 24 6 32 0v-12l-16 8z" fill="#fff"/>
</svg>
<div class="exp-label" style="left:30px;top:3050px"><h4>Passion</h4><p>Demonstrate that you are passionate about farming and that you're in it for the long run</p></div>
<div class="exp-label" style="left:330px;top:3262px"><h4>Professional</h4><p>Be skilled in planning, budgeting and reporting</p></div>
<div class="exp-label" style="left:630px;top:3062px"><h4>Report</h4><p>Report to investors</p></div>
<div class="exp-label" style="left:930px;top:3262px"><h4>Capital</h4><p>Bring your own capital (equipment, livestock, goodwill)</p></div>
<div class="exp-label" style="left:30px;top:3470px"><h4>Share</h4><p>Share your experiences with investors and supporters</p></div>
<div class="exp-label" style="left:330px;top:3662px"><h4>Local community</h4><p>Actively participate in the community</p></div>
<div class="exp-label" style="left:630px;top:3470px"><h4>Standards</h4><p>Ensuring only the best practices are used</p></div>
<div class="exp-label" style="left:930px;top:3662px"><h4>Skills</h4><p>Continually improve your skills as you are farm ready</p></div>

<section class="membership">
  <h3>Making The Most Of Your Membership</h3>
  <p>Here are some tips on how you can make the most of your membership. We encourage you not just to wait for us to find you opportunities, but for you to get out there and help get your farm dream closer to reality.</p>
</section>
<div class="tips">
  <div class="tip">Bring Your Own Retiring Farmer<span class="info">i</span></div>
  <div class="tip">Bring Your Own Investor<span class="info">i</span></div>
  <div class="tip">Build up your skills<span class="info">i</span></div>
  <div class="tip">Talk to the local community<span class="info">i</span></div>
  <div class="tip">Business management skills<span class="info">i</span></div>
  <div class="tip">Business management skills<span class="info">i</span></div>
  <div class="tip">Add to your profile<span class="info">i</span></div>
  <div class="tip">Social media<span class="info">i</span></div>
  <div class="tip">Local bank<span class="info">i</span></div>
  <div class="tip">Get in touch with us<span class="info">i</span></div>
</div>

<section class="band" style="top:4400px">
  <div class="pics">
    <div class="pic p1" role="img" aria-label="Cattle grazing in a green paddock"></div>
    <div class="pic p2" role="img" aria-label="Tractor working a field"></div>
    <div class="pic p3" role="img" aria-label="Rolling farmland under blue sky"></div>
  </div>
  <h2>Your Farm Dream Can Be A Reality.</h2>
</section>

<div class="btn-orange abs" style="top:4740px;left:450px;width:300px;height:36px">Sign up now and lets get you farming</div>

<footer class="site-footer">
  <div class="blog">
    <h5>From The Blog</h5>
    <div class="post"><div class="date"><b>24</b><small>Apr 17</small></div><div><h6>Out of the Griddle Barn into the fire of soil health</h6><span>Posted by Lena Ward</span></div></div>
    <div class="post"><div class="date"><b>21</b><small>Apr 17</small></div><div><h6>Harlow is a cool name, as is Elsie, but then passion for farming</h6><span>Posted by Harlow and Elsie</span></div></div>
  </div>
  <div class="subscribe">
    <h5>Subscribe To Our Newsletter</h5>
    <p>Want to be the first to know about our amazing discount offer?</p>
    <div class="field">Email Address</div>
    <div class="btn-orange">Subscribe</div>
  </div>
  <div class="footer-brand"><span class="dot"></span>Meadowrun Acres</div>
  <div class="footer-bottom">
    ©2017 Meadowrun Acres · Terms of Use · Privacy · Sitemap · Donate
    <div class="socials"><i></i><i></i><i></i><i></i></div>
  </div>
</footer>

</body>
</html>
```